I need a label design to go on our jars of honey. Our company is called Marrowdale Honey Co. The type of honey is called Fernlight Glen Honey. The jars are 1kg. Attached is the label size. Left hand side needs to have nutritional info... as attached. Middle section is our company name, honey type, 1kg & Whangamata, NZ. Right hand side needs to have info as per photo (raw honey etc). I would like to upload more pictures... but I’m unsure how to do this? Thanks, Carla

Target Market(s)

Honey consumers... families

Industry/Entity Type

Food Production

Colors

Designer to choose colors to be used in the design.

Requirements
Must have
• Nutritional info as per upload
• Type of honey & company name as per upload
• 1kg
• Address
Nice to have
• Similar fonts to upload.
• Possibly background image... floral or beach... very faint though.

```html
<!DOCTYPE html>
<html lang="en">
<head>
<meta charset="utf-8">
<title>Marrowdale Honey Co. – Fernlight Glen Honey label</title>
<link rel="stylesheet" href="https://fonts.googleapis.com/css2?family=Arimo:wght@400;700&family=Caveat:wght@400&family=Kaushan+Script&family=Oswald:wght@200;300&display=swap">
<style>
  :root {
    --sea-deep: #3d9ad6;
    --sea-mid: #5fb3d8;
    --surf: #8ccbd8;
    --shore: #9fcfc6;
    --sand: #a9d3c8;
    --white: #ffffff;
    --panel-bg: rgba(236, 244, 250, 0.88);
    --panel-line: #b9cfe2;
    --ink-blue: #2f6ea8;
  }
  * { margin: 0; padding: 0; box-sizing: border-box; }
  html, body { width: 1200px; height: 480px; overflow: hidden; background: #fff; }
  .label {
    position: relative;
    width: 1200px;
    height: 480px;
    overflow: hidden;
    color: var(--white);
  }
  .beach-photo {
    position: absolute; inset: 0;
    background:
      radial-gradient(ellipse 140px 420px at 690px 240px, rgba(255,255,255,0.35), transparent 70%),
      linear-gradient(100deg, var(--sea-deep) 0%, var(--sea-mid) 38%, var(--surf) 55%, var(--shore) 70%, var(--sand) 100%);
  }

  /* Nutrition panel */
  .nutrition-panel {
    position: absolute;
    left: 66px; top: 32px;
    width: 262px; height: 420px;
    background: var(--panel-bg);
    border-radius: 14px;
    color: var(--ink-blue);
    font-family: "Arimo", Arial, sans-serif;
  }
  .panel-heading {
    position: absolute; top: 12px; width: 100%;
    text-align: center; font-size: 14.5px; line-height: 18px; font-weight: 400;
  }
  .nutrition-table {
    position: absolute; left: 16px; top: 56px;
    width: 228px; height: 230px;
    border: 1px solid var(--panel-line);
    font-size: 9.5px;
  }
  .table-title { position: absolute; left: 12px; top: 9px; line-height: 11px; }
  .table-head {
    position: absolute; top: 54px; left: 0; right: 0; height: 48px;
    border-top: 1px solid var(--panel-line);
    border-bottom: 1px solid var(--panel-line);
    font-size: 7.5px; line-height: 8.5px;
  }
  .col-serving { position: absolute; left: 93px; }
  .col-100g { position: absolute; left: 169px; }
  .table-head .col-serving, .table-head .col-100g { top: 12px; }
  .table-rows { position: absolute; top: 115px; left: 0; right: 0; }
  .row { position: relative; height: 16.8px; line-height: 16.8px; }
  .row .nutrient { position: absolute; left: 12px; }
  .notes {
    position: absolute; top: 296px; width: 100%;
    text-align: center; font-size: 9.5px; line-height: 12px;
  }
  .batch-fields {
    position: absolute; left: 17px; top: 362px;
    font-size: 12px; font-weight: 700; line-height: 14.4px;
  }
  .batch-fields span { display: inline-block; width: 84px; }

  /* Centre brand block */
  .brand-line {
    position: absolute; left: 390px; width: 420px;
    text-align: center; font-weight: 400;
  }
  .company-name {
    top: 28px;
    font-family: "Oswald", "Arial Narrow", sans-serif;
    font-weight: 200; font-size: 38px; line-height: 53px;
    letter-spacing: 8px;
  }
  .honey-type {
    top: 150px;
    font-family: "Kaushan Script", cursive;
    font-size: 70px; line-height: 80px;
    transform: rotate(-3deg);
  }
  .weight {
    top: 380px;
    font-family: "Oswald", "Arial Narrow", sans-serif;
    font-weight: 300; font-size: 28px; line-height: 32px;
  }
  .origin {
    top: 414px;
    font-family: "Oswald", "Arial Narrow", sans-serif;
    font-weight: 300; font-size: 14px; line-height: 26px; letter-spacing: 3px;
  }

  /* Right story column */
  .story {
    position: absolute; left: 852px; width: 300px; top: 32px;
    text-align: center;
    font-family: "Caveat", cursive;
    font-size: 21px; line-height: 25px;
  }
  .story p { margin-bottom: 28px; }
  .contact {
    position: absolute; left: 878px; width: 200px; top: 377px;
    text-align: center;
    font-family: "Caveat", cursive;
    font-size: 12px; line-height: 17.6px;
    font-style: normal;
  }
</style>
</head>
<body>
<main class="label">
  <div class="beach-photo" role="img" aria-label="Faint aerial photograph of turquoise sea waves meeting a sandy beach"></div>

  <section class="nutrition-panel">
    <h2 class="panel-heading">100% New Zealand Honey<br>no added ingredients</h2>
    <div class="nutrition-table">
      <div class="table-title">NUTRITIONAL INFORMATION<br>Serving per package: 100<br>Serving size: 10g</div>
      <div class="table-head">
        <div class="col-serving">Average<br>Quantity<br>per serving</div>
        <div class="col-100g">Average<br>Quantity<br>per 100g</div>
      </div>
      <div class="table-rows">
        <div class="row"><span class="nutrient">Energy</span><span class="col-serving">134kj</span><span class="col-100g">1340kj</span></div>
        <div class="row"><span class="nutrient">Protein</span><span class="col-serving">0.04g</span><span class="col-100g">0.4g</span></div>
        <div class="row"><span class="nutrient">Fat total</span><span class="col-serving">0g</span><span class="col-100g">0g</span></div>
        <div class="row"><span class="nutrient">- saturated</span><span class="col-serving">0g</span><span class="col-100g">0g</span></div>
        <div class="row"><span class="nutrient">Carbohydrate</span><span class="col-serving">7.9g</span><span class="col-100g">79.6g</span></div>
        <div class="row"><span class="nutrient">-sugars</span><span class="col-serving">7.8g</span><span class="col-100g">78.1g</span></div>
        <div class="row"><span class="nutrient">Sodium</span><span class="col-serving">1.2mg</span><span class="col-100g">12mg</span></div>
      </div>
    </div>
    <p class="notes">Store upright in a cool, dry place.<br>No refrigeration needed.<br>Not recommended for infants below<br>the age of 12 months.</p>
    <div class="batch-fields">
      <div><span>Best Before</span>:</div>
      <div><span>RMP</span>:</div>
      <div><span>Batch No</span>:</div>
    </div>
  </section>

  <h1 class="brand-line company-name">MARROWDALE<br>HONEY CO.</h1>
  <h2 class="brand-line honey-type">Fernlight<br>Glen Honey</h2>
  <div class="brand-line weight">1kg</div>
  <div class="brand-line origin">WHANGAMATA<br>NEW ZEALAND</div>

  <section class="story">
    <p>Sourced from the idyllic<br>Coromandel Peninsula.</p>
    <p>Our honey comes to you raw &amp;<br>unpasteurised, ensuring it retains<br>all the natural goodness!</p>
    <p>Arohanui<br>Rory, Carla &amp; boys</p>
    <p>‘Marrowdale’ all thanks to God for his<br>awesome creation!</p>
  </section>

  <address class="contact">www.marrowdalehoney.co.nz<br>42 Kowhai Lane<br>Whangamata<br>New Zealand</address>
</main>
</body>
</html>
```